Business card design for holistic health care clinic

We need a double-sided business card design for our holistic health care clinic that integrates our logo design and also its color scheme. My business is called Valmira. It is an integrative medicine clinic. You have already done the logo for me. Please ensure an elegant and upscale design that is not cluttered, but still has all the necessary information (please see below for details).

Target Market(s)

Wellness, fitness, rehabilitation for educated, well-traveled open-minded clients who are focused on natural, organic, balanced and preventive healthcare and lifestyle.

Industry/Entity Type

Medical

Contact Information for Business Card

Modern, clean.

Number of Pages Required

1 page

Font styles to use
Serif
Sans Serif

Colors

Designer to choose colors to be used in the design.

Requirements
Must have
• Logo on one side, all other information on the other side.
• Other information should include:
• Tobias Wrenfeld - DOE, CPT, LMT
• 4100 East Marrow Drive
• Austin, TX 78119
• 512 555 0148
• 818 555 0192
• info@ValmiraHealth.example
• t.wrenfeld@ValmiraHealth.example
Nice to have
• Darker background on front - but not totally black - shaded/dark gray.

```html
<!DOCTYPE html>
<html lang="en">
<head>
<meta charset="UTF-8">
<title>Valmira – Business Card</title>
<link href="https://fonts.googleapis.com/css2?family=Nunito:wght@400;600;700;800&display=swap" rel="stylesheet">
<style>
  :root {
    --canvas-bg: #e9e7e4;
    --card-white: #ffffff;
    --card-charcoal: #333435;
    --card-black: #1b1d1f;
    --brand-blue: #1a8fd0;
    --text-light: #f2f2f2;
    --figure-light: #f4f6f8;
  }
  * { margin: 0; padding: 0; box-sizing: border-box; }
  html, body { width: 1200px; height: 900px; overflow: hidden; }
  body {
    position: relative;
    background: var(--canvas-bg);
    font-family: "Nunito", Arial, sans-serif;
  }
  .card {
    position: absolute;
    overflow: hidden;
    box-shadow: 0 6px 18px rgba(0,0,0,.25);
  }
  .card-front {
    left: 78px; top: 33px; width: 587px; height: 364px;
    background: var(--card-white);
  }
  .card-back {
    left: 388px; top: 505px; width: 566px; height: 352px;
    background: var(--card-black);
  }
  .front-wave { position: absolute; left: 0; top: 0; width: 587px; height: 364px; }
  .brand { position: absolute; text-align: center; color: var(--brand-blue); }
  .brand-name {
    display: flex; align-items: center; justify-content: center; gap: 10px;
    font-weight: 800; letter-spacing: 1px; line-height: 1;
  }
  .brand-dot { border-radius: 50%; background: var(--brand-blue); }
  .brand-tagline { font-weight: 700; }
  .card-front .brand { left: 0; width: 587px; top: 50px; }
  .card-front .brand-name { font-size: 56px; }
  .card-front .brand-dot { width: 14px; height: 14px; }
  .card-front .brand-tagline { font-size: 17px; margin-top: 6px; }
  .card-back .brand { left: 0; width: 566px; top: 152px; }
  .card-back .brand-name { font-size: 52px; }
  .card-back .brand-dot { width: 13px; height: 13px; }
  .card-back .brand-tagline { font-size: 16px; margin-top: 6px; }
  .bone-motif {
    position: absolute; left: 252px; top: 152px; width: 82px; height: 124px;
    border-radius: 40px 40px 20px 20px;
    background: linear-gradient(180deg, var(--figure-light), #cfd5da);
    border: 2px solid var(--brand-blue);
  }
  .contact-list {
    position: absolute; left: 30px; top: 239px;
    list-style: none; color: var(--text-light); font-size: 15.5px;
  }
  .contact-list li { display: flex; align-items: center; gap: 8px; height: 21.3px; }
  .contact-list svg { width: 13px; height: 13px; flex: none; fill: var(--text-light); }
  .person {
    position: absolute; right: 34px; top: 238px; text-align: right;
    color: var(--text-light);
  }
  .person-name { font-size: 19px; font-weight: 800; letter-spacing: .5px; }
  .person-credentials { font-size: 15px; margin-top: 6px; }
  .person-address { font-size: 15.5px; margin-top: 18px; line-height: 1.4; }
</style>
</head>
<body>

<section class="card card-front">
  <svg class="front-wave" viewBox="0 0 587 364" aria-hidden="true">
    <path d="M0 176 C70 200 150 212 230 186 C250 180 262 176 270 172 L320 172 C360 178 420 214 500 206 C540 202 570 186 587 178 L587 364 L0 364 Z" fill="var(--brand-blue)"/>
    <path d="M0 182 C70 206 150 218 230 192 C250 186 262 182 270 178 L320 178 C360 184 420 220 500 212 C540 208 570 192 587 184 L587 364 L0 364 Z" fill="var(--card-charcoal)"/>
  </svg>

  <div class="brand">
    <div class="brand-name"><span class="brand-dot"></span>VALMIRA</div>
    <div class="brand-tagline">Integrative Holistic Medicine</div>
  </div>

  <div class="bone-motif" role="img" aria-label="Decorative vertebra motif"></div>

  <ul class="contact-list">
    <li><svg viewBox="0 0 16 16"><path d="M3 1h3l1.5 4-2 1.2a9 9 0 0 0 4.3 4.3L11 8.5l4 1.5v3a2 2 0 0 1-2 2A12 12 0 0 1 1 3a2 2 0 0 1 2-2z"/></svg>512 555 0148</li>
    <li><svg viewBox="0 0 16 16"><path d="M4 0h8a1 1 0 0 1 1 1v14a1 1 0 0 1-1 1H4a1 1 0 0 1-1-1V1a1 1 0 0 1 1-1zm1 2v10h6V2zm3 11a1 1 0 1 0 0 2 1 1 0 0 0 0-2z"/></svg>818 555 0192</li>
    <li><svg viewBox="0 0 16 16"><path d="M0 3h16v10H0zm1.5 1.5L8 9l6.5-4.5V12h-13z"/></svg>info@ValmiraHealth.example</li>
    <li><svg viewBox="0 0 16 16"><path d="M0 3h16v10H0zm1.5 1.5L8 9l6.5-4.5V12h-13z"/></svg>t.wrenfeld@ValmiraHealth.example</li>
    <li><svg viewBox="0 0 16 16"><circle cx="8" cy="8" r="7.5"/><path d="M1 8h14M8 1c-3 3-3 11 0 14M8 1c3 3 3 11 0 14" stroke="#333435" stroke-width="1.2" fill="none"/></svg>www.ValmiraHealth.example</li>
  </ul>

  <div class="person">
    <div class="person-name">TOBIAS WRENFELD</div>
    <div class="person-credentials">DOE, CPT, LMT</div>
    <div class="person-address">4100 East Marrow Drive<br>Austin, TX 78119</div>
  </div>
</section>

<section class="card card-back">
  <div class="brand">
    <div class="brand-name"><span class="brand-dot"></span>VALMIRA</div>
    <div class="brand-tagline">Integrative Holistic Medicine</div>
  </div>
</section>

</body>
</html>
```